We are a Dog Treat company that is going to sell a product that can be served frozen or room temp

Think about something similar to the mandarin oranges cups sold by tavy. Our product needs to be sealed tight to maintain freshness. We want to sell the product in packs of 4, so a package would have 4 individual cups.
Each cup will contain around 3.5 ounces of product.

I have uploaded some packaging examples, and I uploaded our logo.

Target Market(s)

Dog owners, brixel users, people who purchase dog food online

Industry/Entity Type

It Company

Requirements
Must have
• vacuum seal, logo on box
Nice to have
• logo on each cup

```html
<!DOCTYPE html>
<html lang="en">
<head>
<meta charset="utf-8">
<title>Twin Tails Dog Treats – Box Dieline</title>
<link rel="stylesheet" href="https://fonts.googleapis.com/css2?family=Lobster&family=Open+Sans:wght@400;600&family=Playfair+Display:ital,wght@1,600&display=swap">
<style>
  :root {
    --navy-deep: #0c2466;
    --navy: #173a8c;
    --blue-mid: #2f6cb8;
    --blue-light: #4f8fd0;
    --guide: #3fb8a8;
    --white: #ffffff;
    --ink: #1b1b2b;
    --banner-red: #e3231b;
    --banner-dark: #a8150f;
    --gold: #ffd21f;
    --gold-deep: #f3a712;
    --treat-tan: #c07a3c;
    --treat-dark: #8a4f22;
    --label-grey: #555555;
  }
  html, body {
    margin: 0;
    padding: 0;
    width: 744px;
    height: 1200px;
    overflow: hidden;
    background: var(--white);
  }
  .dieline { display: block; width: 744px; height: 1200px; }
  .script { font-family: "Lobster", cursive; }
  .sans { font-family: "Open Sans", Arial, sans-serif; }
  .serif-italic { font-family: "Playfair Display", Georgia, serif; font-style: italic; font-weight: 600; }
  .tagline { fill: var(--white); font-size: 13px; }
  .count-line { fill: var(--white); font-size: 17px; }
  .product-name { font-size: 52px; fill: url(#goldText); }
  .banner-text { fill: var(--gold); font-size: 17px; }
  .brand-name { fill: var(--navy); font-size: 15px; }
  .small-note { fill: var(--white); font-size: 7.5px; }
  .pill-note { fill: var(--label-grey); font-size: 7px; }
  .window-note { fill: var(--label-grey); font-size: 8px; }
  .mission { fill: var(--ink); font-size: 19px; }
  .guide-line { stroke: var(--guide); stroke-width: 0.7; }
</style>
</head>
<body>
<svg class="dieline" viewBox="0 0 476 768" xmlns="http://www.w3.org/2000/svg" aria-label="Twin Tails dog treats box dieline">
  <defs>
    <linearGradient id="boxBlue" x1="0" y1="0" x2="1" y2="0">
      <stop offset="0" stop-color="var(--navy-deep)"/>
      <stop offset="0.5" stop-color="var(--blue-mid)"/>
      <stop offset="1" stop-color="var(--navy-deep)"/>
    </linearGradient>
    <linearGradient id="panelGlow" x1="0" y1="0" x2="0" y2="1">
      <stop offset="0" stop-color="var(--blue-light)" stop-opacity="0.45"/>
      <stop offset="1" stop-color="var(--navy-deep)" stop-opacity="0.35"/>
    </linearGradient>
    <linearGradient id="goldText" x1="0" y1="0" x2="0" y2="1">
      <stop offset="0" stop-color="#fff6b0"/>
      <stop offset="0.5" stop-color="var(--gold)"/>
      <stop offset="1" stop-color="var(--gold-deep)"/>
    </linearGradient>
    <linearGradient id="treatTone" x1="0" y1="0" x2="1" y2="1">
      <stop offset="0" stop-color="var(--treat-tan)"/>
      <stop offset="1" stop-color="var(--treat-dark)"/>
    </linearGradient>
    <symbol id="brandSeal" viewBox="-44 -44 88 88">
      <circle r="42" fill="var(--white)" stroke="var(--navy-deep)" stroke-width="1"/>
      <text class="script brand-name" text-anchor="middle" y="5">Twin Tails</text>
    </symbol>
    <g id="frontPanel">
      <rect x="4" y="0" width="468" height="120" fill="url(#panelGlow)"/>
      <text class="script tagline" x="100" y="17">Sewed Frozen or Room Temp</text>
      <use href="#brandSeal" x="53" y="16" width="84" height="84"/>
      <text class="script count-line" x="146" y="48">4 Individual cups</text>
      <path d="M300 34 Q340 22 382 30 Q430 40 468 24 L468 56 Q430 70 382 60 Q340 52 300 64 Z" fill="var(--banner-red)" stroke="var(--banner-dark)" stroke-width="1"/>
      <text class="script banner-text" x="306" y="52" transform="rotate(-5 380 46)">Healthy &amp; Fun!</text>
      <text class="script product-name" x="160" y="103">Dog Treats</text>
    </g>
  </defs>

  <!-- box outline -->
  <path d="M20 20 Q20 2 40 2 H440 Q458 2 458 20 V160 H472 V660 H412 V750 Q412 766 396 766 H96 Q80 766 80 750 V660 H4 V160 H20 Z" fill="url(#boxBlue)" stroke="var(--navy-deep)" stroke-width="1"/>

  <!-- top flap (back, upside down) -->
  <text class="sans small-note" x="370" y="16" text-anchor="middle" transform="rotate(180 370 14)">Can be served frozen or at room temperature</text>
  <g class="nutrition-panel">
    <rect x="75" y="65" width="180" height="80" fill="var(--navy-deep)" stroke="#4a6fb0" stroke-width="0.6"/>
    <text class="sans small-note" x="120" y="105" text-anchor="middle" transform="rotate(180 120 103)">Nutrition Facts</text>
  </g>
  <path class="cup-window" d="M282 160 V75 Q282 42 314 42 H360 Q392 42 392 75 V160 Z" fill="var(--white)"/>

  <!-- back panel (upside down) -->
  <rect x="75" y="153" width="110" height="10" rx="5" fill="var(--white)"/>
  <text class="sans pill-note" x="130" y="160" text-anchor="middle" transform="rotate(180 130 158)">open for cup to show</text>
  <rect class="mission-box" x="65" y="172" width="250" height="103" fill="var(--white)"/>
  <g transform="rotate(180 190 223)">
    <text class="serif-italic mission" x="190" y="216" text-anchor="middle">Mission statement is</text>
    <text class="serif-italic mission" x="190" y="240" text-anchor="middle">needed here</text>
  </g>
  <use href="#brandSeal" x="321" y="184" width="84" height="84" transform="rotate(180 363 226)"/>

  <!-- front panels -->
  <use href="#frontPanel" y="285"/>
  <use href="#frontPanel" y="407"/>

  <!-- bottom panel -->
  <rect x="85" y="533" width="120" height="10" rx="5" fill="var(--white)"/>
  <text class="sans pill-note" x="145" y="540.5" text-anchor="middle">open for cup to show</text>
  <path class="cup-window" d="M268 530 V605 Q268 652 313 652 H370 Q415 652 415 605 V530 Z" fill="var(--white)"/>
  <text class="sans window-note" x="276" y="572">open for cup w/ food to show</text>
  <rect class="treat-art" x="55" y="548" width="205" height="100" rx="14" fill="url(#treatTone)" opacity="0.85" role="img" aria-label="Scattered bone-shaped dog biscuits"/>
  <text class="sans small-note" x="380" y="656" font-weight="600">3.5 ounces cups</text>

  <!-- bottom flap -->
  <rect class="barcode-spot" x="93" y="690" width="107" height="60" fill="var(--white)"/>
  <text class="sans pill-note" x="98" y="712">Spot for Barcode</text>

  <!-- fold guides -->
  <line class="guide-line" x1="0" y1="160" x2="476" y2="160"/>
  <line class="guide-line" x1="0" y1="285" x2="476" y2="285"/>
  <line class="guide-line" x1="0" y1="407" x2="476" y2="407"/>
  <line class="guide-line" x1="0" y1="530" x2="476" y2="530"/>
  <line class="guide-line" x1="0" y1="660" x2="476" y2="660"/>
</svg>
</body>
</html>
```